Banner to be displayed at local Farmers Market Booth.

Graphic Design Brief: Farmers Market Banner Contest

Project Overview:We are seeking talented graphic designers to create a visually appealing banner for our booth at the local farmers market. Our company specializes in healthy, all-natural dog and cat treats, and we want a banner that captures our brand identity while drawing in pet owners who value quality and nutrition for their furry friends.

Banner Specifications:

Size: 24 inches x 60 inches (Horizontal orientation) 24" High X 60 wide

Theme: Vintage/Retro

Style: Warm, inviting, nostalgic with a touch of rustic charm

Colors: Earthy, muted tones such as warm browns, soft greens, and creamy yellows. Pops of red or blue may be used sparingly for accents. OR Black and White with gray scales. Would like to see both

Typography: Retro-style fonts that are readable and align with the vintage aesthetic.

Key Elements to Include: website (www.moltbyfarms.com)

Company Name: Moltby Farms

Tagline: " Simply Honest Bites "
Imagery: Illustrations or stylized graphics of happy dogs and cats, possibly interacting with treats.

Emphasis on Natural Ingredients: Icons or design elements that subtly suggest freshness and quality (e.g., leaves, wheat, bones, or paw prints).

Farmers Market Appeal: A design that blends well with the artisanal, handmade, and farm-fresh atmosphere of the market.

Design Considerations:

The banner should be easily readable from a distance.

A balanced composition that doesn't feel overcrowded.

Should evoke trust and warmth while maintaining a professional look.

Avoid overly modern or sleek elements that don’t align with the vintage aesthetic.

Submission Requirements:

High-resolution digital file in PDF or AI format.

CMYK color mode for printing purposes.

Must include a mockup or preview of how it would look in a real farmers market setting.

We look forward to seeing your creative interpretations of our brand! If you have any questions, feel free to reach out.

Font styles to use
Other font styles liked:
• See attachement

Requirements
Nice to have
• Retro/Vintage,playful BUT NOT whimsical

```html
<!DOCTYPE html>
<html lang="en">
<head>
<meta charset="utf-8">
<title>Moltby Farms – Market Banner</title>
<link href="https://fonts.googleapis.com/css2?family=Oswald:wght@600;700&family=Fraunces:opsz,wght@72,900&display=swap" rel="stylesheet">
<style>
  :root {
    --page: #ffffff;
    --frame: #e4e4e2;
    --frame-line: #d2d2cf;
    --gold: #e3a21c;
    --gold-deep: #a8700a;
    --white: #ffffff;
    --pill: #c6c6c6;
    --pill-edge: #555555;
    --ink: #1f1f1f;
    --art-light: #cfcfcf;
    --art-dark: #5e5e5e;
  }
  html, body {
    margin: 0;
    width: 941px;
    height: 1200px;
    overflow: hidden;
    background: var(--page);
  }
  .banner {
    position: absolute;
    left: 30px;
    top: 424px;
    width: 880px;
    height: 352px;
    background: repeating-linear-gradient(90deg, var(--frame) 0 3px, var(--frame-line) 3px 4px);
    box-shadow: 0 14px 40px rgba(0,0,0,.28);
  }
  .banner__panel {
    position: absolute;
    inset: 0;
  }
  .brand-name {
    position: absolute;
    left: 220px;
    top: 28px;
    width: 180px;
    text-align: center;
    font-family: 'Oswald', sans-serif;
    font-weight: 600;
    font-size: 22px;
    letter-spacing: 1px;
    line-height: 1;
    color: var(--white);
  }
  .tagline {
    position: absolute;
    left: 40px;
    top: 64px;
    width: 480px;
    margin: 0;
    text-align: center;
    font-family: 'Oswald', sans-serif;
    font-weight: 700;
    text-transform: uppercase;
    color: var(--white);
    line-height: 1;
    white-space: nowrap;
    text-shadow:
      1px 1px 0 var(--gold), 2px 2px 0 var(--gold), 3px 3px 0 var(--gold),
      4px 3px 0 var(--gold-deep), 5px 4px 0 var(--gold-deep), 6px 5px 0 var(--gold-deep);
  }
  .tagline__line { display: block; }
  .tagline__line--top { font-size: 74px; letter-spacing: 1px; }
  .tagline__line--bottom { font-size: 86px; margin-top: 4px; }
  .web-pill {
    position: absolute;
    left: 64px;
    top: 280px;
    width: 440px;
    height: 46px;
    box-sizing: border-box;
    border: 3px solid var(--white);
    border-radius: 18px;
    background: var(--pill);
    outline: 2px solid var(--pill-edge);
    outline-offset: -6px;
    display: flex;
    align-items: center;
    justify-content: center;
    font-family: 'Fraunces', serif;
    font-weight: 900;
    font-size: 32px;
    line-height: 1;
    color: var(--ink);
  }
  .pet-art {
    position: absolute;
    left: 540px;
    top: 50px;
    width: 300px;
    height: 282px;
    border-radius: 44% 44% 8px 8px;
    background: radial-gradient(ellipse at 58% 45%, var(--art-light), var(--art-dark) 80%);
    opacity: .85;
  }
</style>
</head>
<body>
  <section class="banner">
    <svg class="banner__panel" width="880" height="352" viewBox="0 0 880 352" aria-hidden="true">
      <defs>
        <radialGradient id="panel-glow" cx="45%" cy="50%" r="65%">
          <stop offset="0" stop-color="#3a3a3a"/>
          <stop offset="1" stop-color="#242424"/>
        </radialGradient>
      </defs>
      <path d="M48 16 H832 A30 30 0 0 0 862 46 V306 A30 30 0 0 0 832 336 H48 A30 30 0 0 0 18 306 V46 A30 30 0 0 0 48 16 Z"
            fill="url(#panel-glow)" stroke="#e3a21c" stroke-width="2.5"/>
    </svg>

    <div class="brand-name">Moltby Farms</div>

    <h1 class="tagline">
      <span class="tagline__line tagline__line--top">Simply Honest</span>
      <span class="tagline__line tagline__line--bottom">Bites</span>
    </h1>

    <div class="web-pill">moltbyfarms.com</div>

    <div class="pet-art" role="img" aria-label="Black and white engraved illustration of a kitten sitting beside a golden retriever"></div>
  </section>
</body>
</html>
```